Web design project for exciting Australian start-up

Background
We are looking for a creative and talented web design artist to work alongside our market leading web developer.
• You will be required to create a modern and clean design theme for our website, incorporating selected rustic colour scheme elements for our exciting Australian start-up to operate within the coffee industry.
reoccurring work to be expected to flow to the successful designer.
Requirements
• c. 5 - 10 page website
• Landing page
• Log in/ out
• 404 template
• Typography is emphasised
• Please use either a) typemarrow.com, b) free web fonts, c) brindle fonts
• All design elements in vector format
• Preferably with icons for each header title(i.e. about us, how it works etc) but designer have free reign over how the site looks, so might not be applicable
• All pages to be responsive
• Down to eSlab resolution

High level visual design brief attached - additional pages to be worked from base design.

Design inspiration
• We would like to use design elements from the following sources:
http://www.zandrix.com/halcyon/ (Functionality)
Colour scheme refer to logo and complementary style guide

```html
<!DOCTYPE html>
<html lang="en">
<head>
<meta charset="utf-8">
<title>Bean Haven – Marketplace</title>
<link href="https://fonts.googleapis.com/css2?family=Montserrat:wght@700&family=Questrial&display=swap" rel="stylesheet">
<style>
  :root {
    --orange: #f7931e;
    --orange-dark: #e97f0c;
    --red: #e8383d;
    --ink: #1a1a1a;
    --charcoal: #333333;
    --white: #ffffff;
    --field-text: #8a8a8a;
    --arrow: #b3b3b3;
    --panel-line: rgba(255,255,255,0.85);
    --panel-fill: rgba(20,14,10,0.45);
    --footer-panel: rgba(120,110,104,0.55);
  }
  * { box-sizing: border-box; margin: 0; padding: 0; }
  html, body { width: 1200px; height: 831px; overflow: hidden; }
  body {
    position: relative;
    font-family: "Questrial", "Helvetica Neue", Arial, sans-serif;
    background: #2b1e17;
    color: var(--white);
  }
  a { text-decoration: none; color: inherit; }

  /* Hero photography area */
  .hero-photo {
    position: absolute; left: 0; top: 0; width: 1200px; height: 605px;
    background:
      radial-gradient(ellipse 380px 260px at 860px 300px, rgba(235,228,220,0.55), transparent 70%),
      radial-gradient(ellipse 300px 220px at 120px 160px, rgba(168,140,100,0.55), transparent 70%),
      linear-gradient(180deg, #3a2418 0%, #4a2c1c 45%, #6b3f24 75%, #5a341f 100%);
  }

  /* Header */
  .site-header {
    position: absolute; left: 0; top: 0; width: 1200px; height: 123px;
    background: rgba(245,242,238,0.86);
    border-bottom: 1px solid rgba(255,255,255,0.9);
  }
  .brand {
    position: absolute; left: 74px; top: 44px;
    display: flex; align-items: center; gap: 12px;
    font-family: "Montserrat", Arial, sans-serif; font-weight: 700;
    font-size: 30px; color: var(--ink); white-space: nowrap;
  }
  .brand-dot {
    width: 22px; height: 22px; border-radius: 50%; background: var(--orange); flex: none;
  }
  .account-nav {
    position: absolute; left: 835px; top: 46px;
    display: flex; align-items: center;
    font-family: "Montserrat", Arial, sans-serif; font-weight: 700; font-size: 11px;
    white-space: nowrap;
  }
  .account-link { color: var(--ink); width: 94px; }
  .nav-button {
    height: 30px; display: flex; align-items: center; justify-content: center;
    color: var(--white); border-radius: 2px; white-space: nowrap;
  }
  .nav-button--active { background: var(--orange); width: 86px; }
  .nav-button--logout { background: var(--charcoal); width: 69px; margin-left: 7px; }

  /* Marketplace intro */
  .page-title {
    position: absolute; left: 74px; top: 275px; width: 266px; height: 50px;
    background: rgba(0,0,0,0.6);
    font-family: "Montserrat", Arial, sans-serif; font-weight: 700;
    font-size: 36px; color: var(--orange);
    padding-left: 12px; line-height: 50px; white-space: nowrap;
  }
  .cta {
    display: flex; align-items: center; gap: 12px;
    font-family: "Montserrat", Arial, sans-serif; font-weight: 700;
    color: var(--white); letter-spacing: 0.6px; border-radius: 2px; white-space: nowrap;
  }
  .cta svg { flex: none; }
  .cta--tender {
    position: absolute; left: 74px; top: 350px; width: 180px; height: 43px;
    background: var(--red); font-size: 14px; padding-left: 18px;
  }

  /* Search panel */
  .search-panel {
    position: absolute; left: 547px; top: 155px; width: 579px; height: 306px;
    border: 1.5px solid var(--panel-line); border-radius: 2px;
    background: var(--panel-fill);
  }
  .search-title {
    position: absolute; left: 27px; top: 18px; font-size: 26px; font-weight: 400;
  }
  .field {
    position: absolute; width: 163px; height: 37px; background: var(--white);
    border-radius: 2px; color: var(--field-text); font-size: 12.5px;
    padding-left: 13px; line-height: 37px;
  }
  .field::before, .field::after {
    content: ""; position: absolute; right: 10px;
    border-left: 7px solid transparent; border-right: 7px solid transparent;
  }
  .field::before { top: 11px; border-bottom: 5px solid var(--arrow); }
  .field::after { top: 21px; border-top: 5px solid var(--arrow); }
  .col-1 { left: 28px; } .col-2 { left: 209px; } .col-3 { left: 390px; }
  .row-1 { top: 64px; } .row-2 { top: 118px; } .row-3 { top: 174px; }
  .cta--search {
    position: absolute; left: 28px; top: 236px; width: 197px; height: 45px;
    background: linear-gradient(180deg, var(--orange), var(--orange-dark));
    font-size: 14px; padding-left: 18px;
  }

  /* Footer */
  .site-footer {
    position: absolute; left: 0; top: 605px; width: 1200px; height: 226px;
    background: linear-gradient(90deg, #2e211a, #3b2c23 50%, #2e211a);
  }
  .footer-panel {
    position: absolute; left: 74px; top: 20px; width: 1052px; height: 191px;
    background: var(--footer-panel); border-radius: 3px;
  }
  .footer-col { position: absolute; top: 22px; }
  .footer-col h3 {
    font-family: "Montserrat", Arial, sans-serif; font-weight: 700;
    font-size: 11px; letter-spacing: 0.4px; margin-bottom: 12px;
  }
  .footer-col ul { list-style: none; }
  .footer-col li {
    font-size: 11px; color: var(--orange); height: 26px;
    display: flex; align-items: flex-start; gap: 14px; white-space: nowrap;
  }
  .footer-col--info { left: 28px; } .footer-col--about { left: 199px; } .footer-col--social { left: 363px; }
  .social-square { width: 14px; height: 14px; background: #5a6e8c; border-radius: 2px; flex: none; }
  .footer-brand {
    position: absolute; right: 29px; top: 36px;
    display: flex; align-items: center; gap: 8px;
    font-family: "Montserrat", Arial, sans-serif; font-weight: 700;
    font-size: 19px; color: var(--white); white-space: nowrap;
  }
  .footer-brand .brand-dot { width: 14px; height: 14px; }
  .copyright {
    position: absolute; right: 29px; top: 113px; text-align: right;
    font-size: 11px; line-height: 17px;
  }
  .copyright span { color: var(--orange); }
</style>
</head>
<body>
  <div class="hero-photo" role="img" aria-label="Photograph of coffee beans spilling from a hessian sack onto a wooden table beside a white cup of coffee with cinnamon sticks and star anise"></div>

  <header class="site-header">
    <div class="brand"><span class="brand-dot"></span>Bean Haven</div>
    <nav class="account-nav">
      <a class="account-link" href="#">MY ACCOUNT</a>
      <span class="nav-button nav-button--active">LOGGED IN</span>
      <span class="nav-button nav-button--logout">LOG OUT</span>
    </nav>
  </header>

  <h1 class="page-title">Marketplace</h1>
  <a class="cta cta--tender" href="#">
    <svg width="16" height="16" viewBox="0 0 16 16"><path d="M1 1 L15 8 L1 15 L5 8 Z" fill="#fff"/></svg>
    START TENDER
  </a>

  <form class="search-panel">
    <h2 class="search-title">Select</h2>
    <div class="field col-1 row-1">Tender type</div>
    <div class="field col-2 row-1">Quantity (kg)</div>
    <div class="field col-3 row-1">Wholesaler</div>
    <div class="field col-1 row-2">Tender type</div>
    <div class="field col-2 row-2">Tender type</div>
    <div class="field col-1 row-3">Tender type</div>
    <a class="cta cta--search" href="#">
      <svg width="16" height="16" viewBox="0 0 16 16"><path d="M1 1 L15 8 L1 15 L5 8 Z" fill="#fff"/></svg>
      LAUNCH SEARCH
    </a>
  </form>

  <footer class="site-footer" role="contentinfo">
    <div class="footer-panel">
      <div class="footer-col footer-col--info">
        <h3>HELPFUL INFO</h3>
        <ul><li>About us</li><li>Media enquiries</li><li>Terms &amp; conditions</li><li>Privacy policy</li></ul>
      </div>
      <div class="footer-col footer-col--about">
        <h3>WHO WE ARE</h3>
        <ul><li>How it works</li><li>FAQ</li><li>Contact us</li></ul>
      </div>
      <div class="footer-col footer-col--social">
        <h3>JOIN US</h3>
        <ul>
          <li><span class="social-square"></span>Pagebook</li>
          <li><span class="social-square"></span>Chirper</li>
          <li><span class="social-square"></span>Workline</li>
          <li><span class="social-square"></span>Clipstream</li>
        </ul>
      </div>
      <div class="footer-brand"><span class="brand-dot"></span>Bean Haven</div>
      <p class="copyright">Copyright © 2014 <span>Bean Haven</span><br>All Right Reserved</p>
    </div>
  </footer>
</body>
</html>
```